ORLA - Óptica Médica - web design and concept

Website concept - Create and develop our website design and structure. ORLA is an optical store chain, and we are looking to establish our web and digital concept. In attachment there are several pictures about our stores and our logo.

The website structure should be user friendly. Colors should be light and the design as simple and minimalist as possible. There are different variations of the logothat can be used, check the file.

The website will include optical collections and sun collections as an online store. Also, a medical menu should be considered in order for clients to schedule optometry appointments. There should also be a menu for client assistance where the clients can read about glass maintenance in our workshop.
Updates

Low design quality

Number of Pages Required

5+ page

Font styles to use
Serif
Sans Serif

Requirements
Must have
• Must be user-friendly and minimalist.
• Please USE PICTURES FROM THE BRANDS we sell: MERUN, BOSKA, PNW, KOLE, BAMPE
Nice to have
• Nice to inspire: ZEK glasses (see website https://ch.shopzek.com/en/)
• Nice to inspire: https://merun-eyewear.com/
• Nice to ispire: https://www.pnwglobe.com/en/
Should not have
• Hysteric colors and shapes

```html
<!DOCTYPE html>
<html lang="en">
<head>
<meta charset="utf-8">
<title>ORLA — Company History</title>
<link rel="stylesheet" href="https://fonts.googleapis.com/css2?family=Lato:wght@300;400;700&display=swap">
<style>
:root{
  --ink:#111;
  --text:#222;
  --accent:#e8a23a;
  --line:#d8d8d8;
  --band:#f5f6f8;
  --footer:#000;
  --white:#fff;
}
*{margin:0;padding:0;box-sizing:border-box}
html,body{width:1200px;height:2261px;overflow:hidden;background:var(--white)}
body{position:relative;font-family:'Lato',sans-serif;color:var(--text)}
.abs{position:absolute}

/* header */
.social{display:flex;gap:9px;align-items:center}
.social span{width:9px;height:9px;border-radius:50%;background:var(--ink);display:block}
.brand{left:0;width:1200px;top:34px;text-align:center;color:var(--ink);font-size:26px;font-weight:400;line-height:1}
.util{top:15px;font-size:11px;display:flex;align-items:center;gap:6px;color:var(--ink)}
.nav{top:106px;left:0;width:1200px;display:flex;justify-content:center;align-items:center;gap:20px;font-size:11.5px;color:var(--ink)}
.nav .current{color:var(--accent)}
.nav .cta{background:var(--ink);color:var(--white);padding:5px 7px}

.page-title{top:205px;left:0;width:1200px;text-align:center;font-size:46px;font-weight:300;color:var(--ink)}

/* story sections */
.story h2{font-size:27px;font-weight:300;color:var(--ink);line-height:1}
.rule{width:134px;height:5px;border-top:1px solid var(--accent);border-bottom:1px solid var(--accent);margin-top:12px}
.story p{font-size:11.3px;line-height:14.2px;margin-top:16px;width:410px;color:var(--ink)}
.btn{display:flex;align-items:center;justify-content:center;width:182px;height:51px;border:2px solid var(--ink);font-size:12.5px;color:var(--ink);letter-spacing:.3px}
.photo{display:block}

/* features */
.feature{border:2px solid var(--line);height:89px;display:flex;align-items:center;justify-content:center;gap:14px;top:1428px}
.feature b{display:block;font-weight:300;font-size:17px;color:var(--ink)}
.feature small{display:block;font-size:10.5px;color:var(--ink)}

/* partners */
.partners{top:1554px;left:0;width:1200px;height:163px;background:var(--band);border-top:1px solid #e6e6e6;border-bottom:1px solid #e6e6e6}
.partner{top:66px;width:170px;margin-left:-85px;text-align:center;font-size:24px;font-weight:400;color:var(--ink)}

/* newsletter */
.news-title{top:1752px;left:0;width:1200px;text-align:center;font-size:27px;font-weight:300;color:var(--ink)}
.news-rule{top:1790px;left:535px;width:130px;height:5px;border-top:1px solid var(--accent);border-bottom:1px solid var(--accent)}
.news-input{top:1829px;left:304px;width:506px;height:70px;border:2px solid var(--line);border-right:none;font-size:11px;padding-left:30px;display:flex;align-items:center;color:var(--ink)}
.news-send{top:1829px;left:808px;width:92px;height:70px;border:2px solid var(--ink);display:flex;align-items:center;justify-content:center}

/* footer */
.footer{top:1936px;left:0;width:1200px;height:325px;background:var(--footer);color:var(--white)}
.foot-brand{left:163px;top:70px;font-size:22px;font-weight:400;line-height:1;color:var(--white)}
.foot-about{left:163px;top:120px;width:155px;font-size:10.5px;line-height:13px}
.foot-more{left:163px;top:164px;font-size:11px}
.footer .social span{background:var(--white)}
.foot-col{top:92px}
.foot-col h3{font-size:13px;font-weight:700;margin-bottom:16px}
.foot-col ul{list-style:none;font-size:11px;line-height:16.5px}
.foot-col li::before{content:"";display:inline-block;width:3px;height:3px;background:var(--accent);border-radius:50%;margin:0 10px 2px 2px;vertical-align:middle}
.contact li::before{display:none}
.contact li{display:flex;gap:8px;align-items:flex-start;margin-bottom:8px;line-height:15px}
.foot-rule{top:224px;left:163px;width:879px;height:1px;background:#666}
.foot-legal{top:238px;font-size:12px}
</style>
</head>
<body>

<header>
  <div class="abs social" style="left:163px;top:18px"><span></span><span></span><span></span><span></span><span></span></div>
  <div class="abs brand">ORLA</div>
  <div class="abs util" style="left:820px">
    <svg width="10" height="11" viewBox="0 0 10 11"><rect x="1" y="4" width="8" height="7" fill="#111"/><path d="M3 4V2.5a2 2 0 0 1 4 0V4" stroke="#111" fill="none"/></svg>
    Your Cart &nbsp;( 0 )
  </div>
  <div class="abs util" style="left:936px">
    <svg width="10" height="10" viewBox="0 0 10 10"><path d="M2 0l2 2.5-1 1.3a6 6 0 0 0 3 3l1.3-1L10 8l-1.5 2C4 10 0 6 0 1.5z" fill="#111"/></svg>
    +000-555-210-4
  </div>
  <nav class="abs nav">
    <span>Home</span><span>Online store</span><span class="current">Company history</span><span>Medical section</span><span>Store</span><span>Contact Us</span><span class="cta">Make an Appoinment</span>
  </nav>
</header>

<h1 class="abs page-title">Company History</h1>

<section class="abs story" style="left:163px;top:380px">
  <h2>History</h2><div class="rule"></div>
  <p>Lorem Ipsum is simply dummy text of the printing and typesetting industry. Lorem Ipsum has been the industry's standard dummy text ever since the 1500s, when an unknown printer took a galley of type and scrambled it to make a type specimen book. It has survived not only five centuries, but also the leap into electronic typesetting, remaining essentially unchanged. It was popularised in the 1960s with the release of Lettrex sheets containing Lorem Ipsum passages, and more recently with desktop publishing software like Pagemill Desk including versions of Lorem Ipsum.</p>
</section>
<a class="abs btn" style="left:163px;top:570px">READ MORE</a>
<svg class="abs photo" style="left:600px;top:366px" width="440" height="266" role="img" aria-label="Video still of an optician adjusting a lens measuring instrument">
  <defs><linearGradient id="labTone" x1="0" y1="0" x2="1" y2="1"><stop offset="0" stop-color="#5e5450"/><stop offset=".6" stop-color="#a3a3a0"/><stop offset="1" stop-color="#cfcfcb"/></linearGradient></defs>
  <rect width="440" height="266" fill="url(#labTone)"/>
  <circle cx="222" cy="133" r="29" fill="var(--accent)"/>
  <path d="M212 118l26 15-26 15z" fill="#fff"/>
</svg>

<svg class="abs photo" style="left:160px;top:707px" width="440" height="265" role="img" aria-label="Rows of colourful eyeglass frames on a display wall">
  <defs><linearGradient id="frameTone" x1="0" y1="0" x2="1" y2="1"><stop offset="0" stop-color="#d9ecf5"/><stop offset=".5" stop-color="#9fc6db"/><stop offset="1" stop-color="#6f9fbb"/></linearGradient></defs>
  <rect width="440" height="265" fill="url(#frameTone)"/>
</svg>
<section class="abs story" style="left:630px;top:713px">
  <h2>Our Frames</h2><div class="rule"></div>
  <p>Lorem Ipsum is simply dummy text of the printing and typesetting industry. Lorem Ipsum has been the industry's standard dummy text ever since the 1500s, when an unknown printer took a galley of type and scrambled it to make a type specimen book. It has survived not only five centuries, but also the leap into electronic typesetting, remaining essentially unchanged. It was popularised in the 1960s with the release of Lettrex sheets containing Lorem Ipsum passages, and more recently with desktop publishing software like Pagemill Desk including versions of Lorem Ipsum.</p>
</section>
<a class="abs btn" style="left:630px;top:901px">READ MORE</a>

<section class="abs story" style="left:163px;top:1062px">
  <h2>Our Lenses</h2><div class="rule"></div>
  <p>Lorem Ipsum is simply dummy text of the printing and typesetting industry. Lorem Ipsum has been the industry's standard dummy text ever since the 1500s, when an unknown printer took a galley of type and scrambled it to make a type specimen book. It has survived not only five centuries, but also the leap into electronic typesetting, remaining essentially unchanged. It was popularised in the 1960s with the release of Lettrex sheets containing Lorem Ipsum passages, and more recently with desktop publishing software like Pagemill Desk including versions of Lorem Ipsum.</p>
</section>
<a class="abs btn" style="left:163px;top:1251px">READ MORE</a>
<svg class="abs photo" style="left:600px;top:1049px" width="440" height="264" role="img" aria-label="Dark eyeglasses resting in front of an eye chart">
  <defs><radialGradient id="chartTone" cx=".5" cy=".6" r=".7"><stop offset="0" stop-color="#f2f2f2"/><stop offset="1" stop-color="#cfcfcf"/></radialGradient></defs>
  <rect width="440" height="264" fill="url(#chartTone)"/>
</svg>

<div class="abs feature" style="left:167px;width:285px">
  <svg width="22" height="26" viewBox="0 0 22 26"><circle cx="11" cy="10" r="9" fill="none" stroke="#111" stroke-width="1.5"/><path d="M8 19v5h6v-5" fill="none" stroke="#111" stroke-width="1.5"/></svg>
  <div><b>Free Shipping</b><small>Lorem Ipsum is dummy text.</small></div>
</div>
<div class="abs feature" style="left:461px;width:285px">
  <svg width="26" height="26" viewBox="0 0 26 26"><circle cx="13" cy="11" r="8" fill="none" stroke="#111" stroke-width="1.5"/><path d="M4 24c2-5 16-5 18 0" fill="none" stroke="#111" stroke-width="1.5"/><circle cx="13" cy="11" r="2.5" fill="#111"/></svg>
  <div><b>Premium Support</b><small>24/7 Customer service</small></div>
</div>
<div class="abs feature" style="left:754px;width:286px">
  <svg width="38" height="24" viewBox="0 0 38 24"><rect x="1" y="2" width="22" height="15" fill="none" stroke="#111" stroke-width="1.5"/><path d="M23 7h8l5 6v4H23z" fill="none" stroke="#111" stroke-width="1.5"/><circle cx="8" cy="19" r="3" fill="#fff" stroke="#111" stroke-width="1.5"/><circle cx="29" cy="19" r="3" fill="#fff" stroke="#111" stroke-width="1.5"/></svg>
  <div><b>Payment Method</b><small>Cash On Delivery</small></div>
</div>

<section class="abs partners">
  <svg class="abs" style="left:80px;top:60px" width="22" height="44" viewBox="0 0 22 44"><path d="M20 2L2 22l18 20" fill="none" stroke="#111" stroke-width="2"/></svg>
  <div class="abs partner" style="left:234px">Ravelle</div>
  <div class="abs partner" style="left:419px">Solenne</div>
  <div class="abs partner" style="left:603px">Mara Lisle</div>
  <div class="abs partner" style="left:784px">Corvan</div>
  <div class="abs partner" style="left:972px">Tessa Optic</div>
  <svg class="abs" style="left:1104px;top:60px" width="22" height="44" viewBox="0 0 22 44"><path d="M2 2l18 20L2 42" fill="none" stroke="var(--accent)" stroke-width="2"/></svg>
</section>

<h2 class="abs news-title">Subscribe For Our Newsletter</h2>
<div class="abs news-rule"></div>
<div class="abs news-input">E-Mail Address</div>
<div class="abs news-send">
  <svg width="36" height="28" viewBox="0 0 36 28"><path d="M2 2l32 12L2 26l6-12z M8 14h26" fill="none" stroke="#111" stroke-width="1.8" stroke-linejoin="round"/></svg>
</div>

<footer class="abs footer">
  <div class="abs foot-brand">ORLA</div>
  <p class="abs foot-about">Lorem Ipsum is simply dummy text of the printing and typesetting industry.</p>
  <div class="abs foot-more">READ MORE....</div>
  <div class="abs social" style="left:163px;top:192px"><span></span><span></span><span></span><span></span><span></span></div>

  <div class="abs foot-col" style="left:425px"><h3>QUICK LINK</h3>
    <ul><li>Women</li><li>Men</li><li>Youth</li><li>Collections</li><li>Contact Us</li></ul></div>
  <div class="abs foot-col" style="left:638px"><h3>ACCOUNT</h3>
    <ul><li>My Account</li><li>My Wishlist</li><li>Checkout</li><li>Create Account</li><li>Register</li></ul></div>
  <div class="abs foot-col contact" style="left:861px"><h3>QUICK CONTACT</h3>
    <ul>
      <li><svg width="9" height="9" viewBox="0 0 10 10"><path d="M2 0l2 2.5-1 1.3a6 6 0 0 0 3 3l1.3-1L10 8l-1.5 2C4 10 0 6 0 1.5z" fill="var(--accent)"/></svg>+000-555-210-8</li>
      <li><svg width="10" height="8" viewBox="0 0 10 8"><rect width="10" height="8" fill="var(--accent)"/><path d="M0 0l5 4 5-4" stroke="#000" fill="none"/></svg>hello@orlaoptica.example</li>
      <li><svg width="8" height="11" viewBox="0 0 8 11"><path d="M4 11C1 7 0 5.5 0 4a4 4 0 0 1 8 0c0 1.5-1 3-4 7z" fill="var(--accent)"/><circle cx="4" cy="4" r="1.4" fill="#000"/></svg>14 Linden Row,<br>Fairhollow, ST 00420</li>
    </ul></div>

  <div class="abs foot-rule"></div>
  <div class="abs foot-legal" style="left:163px">CopyRight &nbsp;©2018 Orla. All Right Reserve</div>
  <div class="abs foot-legal" style="left:822px">Privacy Policy - Terms &amp; Conditions</div>
</footer>

</body>
</html>
```